Business Cards for IT Consulting Company (Managed Service Provider)

I am looking to have some business cards printed and would like some designs. We are an IT Consulting company based in Vancouver BC. I would like a nice clean and modern look to the cards. I have uploaded all the versions of my logo so parts can be used as needed. Here is a snippit from our website homepage:

Quillbrook Networks Ltd. is an IT Solutions Partner located in Vancouver BC, Canada. We offer IT solutions and support to customers in the greater Vancouver Area. With expertise in Microsoft platforms, as well as Linux and Mac OSX and over 12 years experience in the IT industry, Quillbrook Networks is dedicated to offering our clients top quality service and products. We take pride in the solutions we offer our customers. The greatest compliment a client can give us is to recommend our services.

Quillbrook Networks Ltd. offers a wide range of IT services from onsite service to remote support and managed service solutions. This allows clients to choose the support path that best suits their company’s needs. Supporting many different sized companies from small to enterprise level over the past 12 years Quillbrook Networks has the experience and expertise needed to ensure things run smoothly. Allowing our clients to focus on doing business.

Revolutionizing the way IT services are delivered.

Quillbrook Networks is dedicated to providing our clients with IT solutions that work and grow with them for years to come. This philosophy helps save money in the long run instead of replacing equipment constantly. Far too often IT solutions are not well thought out and while possibly solving the problem at hand, require replacement due to growth or quality within a very short time frame. Quillbrook Networks takes pride in providing solutions that will last and be able to accommodate growth without the need for replacement.

Industry/Entity Type

Information Technology

Contact Information for Business Card

Quillbrook Networks Ltd.
(Employee Name)
Eml: (Employees Email Address)
Web: quillbrook.me
Ph: 604-555-0148

Font styles to use
Serif
Sans Serif

Requirements
Must have
• The Company logo and company colors.
Nice to have
• - Our tag line: "Revolutionizing IT Services" or "Revolutionizing the way IT services are delivered."
• - Also I really like the idea of nature and technology together blending which is sort of where my logo came from so integrating that somehow onto the business cards would be great.

```html
<!DOCTYPE html>
<html lang="en">
<head>
<meta charset="utf-8">
<title>Quillbrook Networks Ltd. – Business Cards</title>
<link rel="stylesheet" href="https://fonts.googleapis.com/css2?family=Open+Sans:wght@400;600;700&display=swap">
<style>
  :root {
    --backdrop: #3d3d3f;
    --card-white: #ffffff;
    --brand-blue: #11a7e6;
    --brand-blue-deep: #0f9fdc;
    --slate: #5f6064;
    --ink: #555659;
    --white: #ffffff;
  }
  * { margin: 0; padding: 0; box-sizing: border-box; }
  html, body {
    width: 1105px;
    height: 1200px;
    overflow: hidden;
    background: var(--backdrop);
    font-family: "Open Sans", Arial, sans-serif;
  }
  .sheet { position: relative; width: 1105px; height: 1200px; }

  .card {
    position: absolute;
    left: 192px;
    width: 720px;
    height: 411px;
    box-shadow: 0 4px 10px rgba(0,0,0,0.45);
    overflow: hidden;
  }
  .card--front { top: 146px; background: var(--card-white); }
  .card--back  { top: 602px; background: var(--brand-blue); }

  /* Front: wordmark */
  .wordmark {
    position: absolute;
    left: 50px;
    top: 70px;
    display: flex;
    align-items: center;
    gap: 18px;
    color: var(--brand-blue);
    font-weight: 600;
  }
  .wordmark__square {
    width: 62px;
    height: 62px;
    background: var(--brand-blue);
  }
  .wordmark__name { line-height: 1; }
  .wordmark__primary { display: block; font-size: 58px; letter-spacing: -0.5px; }
  .wordmark__secondary { display: block; font-size: 24px; letter-spacing: 0.5px; margin-top: 4px; }

  /* Front: name band */
  .name-band {
    position: absolute;
    left: 0;
    top: 257px;
    width: 363px;
    height: 110px;
    background: var(--brand-blue);
    color: var(--white);
    padding: 9px 0 0 49px;
  }
  .name-band__name {
    font-size: 29px;
    font-weight: 600;
    letter-spacing: 0.3px;
    line-height: 1.2;
  }
  .name-band__address {
    font-size: 18.5px;
    line-height: 1.45;
    margin-top: 2px;
  }

  .contact-list {
    position: absolute;
    left: 410px;
    top: 272px;
    list-style: none;
    color: var(--ink);
    font-size: 18.5px;
  }
  .contact-list__item {
    display: flex;
    align-items: center;
    gap: 10px;
    height: 27.5px;
  }
  .contact-list__icon { width: 18px; height: 18px; flex: none; }

  .accent-block {
    position: absolute;
    right: 0;
    top: 257px;
    width: 62px;
    height: 110px;
    background: var(--slate);
  }

  /* Back */
  .back-pattern {
    position: absolute;
    inset: 0;
    background: linear-gradient(135deg, var(--brand-blue) 0%, var(--brand-blue-deep) 100%);
  }
  .back-mark {
    position: absolute;
    left: 305px;
    top: 156px;
    width: 110px;
    height: 110px;
    border: 4px solid var(--white);
    border-radius: 50%;
  }
  .tagline {
    position: absolute;
    left: 0;
    right: 0;
    top: 325px;
    text-align: center;
    color: var(--white);
    font-size: 19.5px;
    font-weight: 600;
  }
</style>
</head>
<body>
<main class="sheet">

  <section class="card card--front" aria-label="Business card front">
    <div class="wordmark">
      <span class="wordmark__square" aria-hidden="true"></span>
      <span class="wordmark__name">
        <span class="wordmark__primary">Quillbrook</span>
        <span class="wordmark__secondary">NETWORKS LTD.</span>
      </span>
    </div>

    <div class="name-band">
      <p class="name-band__name">DANA MERCER</p>
      <p class="name-band__address">2140 Larkspur Lane<br>Burnaby, British Columbia</p>
    </div>

    <ul class="contact-list">
      <li class="contact-list__item">
        <svg class="contact-list__icon" viewBox="0 0 24 24" aria-hidden="true">
          <path fill="#11a7e6" d="M6.6 10.8a15.2 15.2 0 0 0 6.6 6.6l2.2-2.2c.3-.3.7-.4 1-.2 1.1.4 2.3.6 3.6.6.6 0 1 .4 1 1V20c0 .6-.4 1-1 1A17 17 0 0 1 3 4c0-.6.4-1 1-1h3.5c.6 0 1 .4 1 1 0 1.3.2 2.5.6 3.6.1.3 0 .7-.2 1z"/>
        </svg>
        <span>604-555-0148</span>
      </li>
      <li class="contact-list__item">
        <svg class="contact-list__icon" viewBox="0 0 24 24" aria-hidden="true">
          <rect x="2" y="5" width="20" height="14" rx="1.5" fill="#11a7e6"/>
          <path d="M3 6.5l9 6.5 9-6.5" fill="none" stroke="#ffffff" stroke-width="1.6"/>
        </svg>
        <span>dmercer@quillbrook.me</span>
      </li>
      <li class="contact-list__item">
        <svg class="contact-list__icon" viewBox="0 0 24 24" aria-hidden="true">
          <circle cx="12" cy="12" r="10" fill="#11a7e6"/>
          <path d="M2 12h20M12 2c3 3 3 17 0 20M12 2c-3 3-3 17 0 20" fill="none" stroke="#ffffff" stroke-width="1.4"/>
        </svg>
        <span>www.quillbrook.me</span>
      </li>
    </ul>

    <div class="accent-block" aria-hidden="true"></div>
  </section>

  <section class="card card--back" aria-label="Business card back">
    <div class="back-pattern" role="img" aria-label="Faint repeating geometric pattern in lighter blue tones"></div>
    <div class="back-mark" aria-hidden="true"></div>
    <p class="tagline">Revolutionizing IT Services</p>
  </section>

</main>
</body>
</html>
```